American cannabis tech company business card design

Pavrel.com is seeking a modern, professional, and brand-aligned business card that represents our company and its core values: Mission, Story, Values, and Impact. As an innovative cannabis company, we want a business card that is not only visually appealing but also serves as a representation of who we are and what we stand for.

Project Scope: Design a double-sided business card that integrates our brand identity and core values. Incorporate our key brand elements, ensuring a sleek and contemporary aesthetic. Visually reflect our core values (Mission, Story, Values, Impact) in a way that is engaging yet professional.

Target Market(s)

Vendors, third parties,

Contact Information for Business Card

Contact details (name, title, email, phone, website, etc.)

Font styles to use
Other font styles liked:
• Caslon, Centra

Colors

Designer to choose colors to be used in the design.

Requirements
Must have
• Pavrel.com logo and branding A creative yet clean way to integrate our core values (Mission, Story, Values, Impact) Modern typography and a well-structured layout
Nice to have
• forest green, grey, white, black
Should not have
• references to marijuana, leafs, plants, or related product

```html
<!DOCTYPE html>
<html lang="en">
<head>
<meta charset="utf-8">
<title>Pavrel.com — Business Card</title>
<link rel="stylesheet" href="https://fonts.googleapis.com/css2?family=Libre+Caslon+Text:wght@400;700&family=Montserrat:wght@400;500&display=swap">
<style>
  :root {
    --stage: #1c1c1c;
    --forest: #1b3320;
    --forest-deep: #112417;
    --forest-panel: #263b29;
    --brand-green: #1b3a20;
    --paper: #ffffff;
    --ink-light: #f3f5f2;
  }
  * { box-sizing: border-box; margin: 0; padding: 0; }
  html, body {
    width: 1200px;
    height: 1015px;
    overflow: hidden;
    background: var(--stage);
  }
  .stage {
    width: 1200px;
    height: 1015px;
    display: flex;
    flex-direction: column;
    align-items: center;
    justify-content: center;
    gap: 56px;
  }
  .card {
    width: 760px;
    height: 434px;
    position: relative;
    overflow: hidden;
    box-shadow: 0 18px 40px rgba(0,0,0,0.55);
  }

  /* Front */
  .card-front {
    background: var(--forest);
    display: flex;
    align-items: center;
    justify-content: center;
  }
  .wordmark {
    font-family: "Libre Caslon Text", serif;
    font-weight: 700;
    letter-spacing: 0.02em;
    line-height: 1;
  }
  .card-front .wordmark {
    font-size: 132px;
    color: var(--forest-deep);
  }

  /* Back */
  .card-back {
    display: flex;
    background: var(--paper);
  }
  .info-panel {
    width: 52%;
    background: var(--forest-panel);
    color: var(--ink-light);
    padding: 64px 0 0 56px;
    position: relative;
  }
  .person-name {
    font-family: "Libre Caslon Text", serif;
    font-weight: 700;
    font-size: 24px;
  }
  .person-title {
    font-family: "Libre Caslon Text", serif;
    font-weight: 700;
    font-size: 12px;
    margin: 4px 0 0 14px;
  }
  .contact-block {
    position: absolute;
    left: 150px;
    bottom: 46px;
    font-family: "Montserrat", sans-serif;
    font-size: 15px;
    line-height: 1.3;
    color: var(--ink-light);
  }
  .address { margin-bottom: 14px; }
  .contact-list { list-style: none; padding-left: 6px; }
  .contact-list li {
    display: flex;
    align-items: center;
    gap: 10px;
    margin-top: 4px;
  }
  .contact-list svg { width: 14px; height: 14px; flex: none; }
  .brand-panel {
    flex: 1;
    display: flex;
    align-items: center;
    justify-content: center;
  }
  .brand-panel .wordmark {
    font-size: 62px;
    color: var(--brand-green);
  }
</style>
</head>
<body>
<main class="stage">
  <section class="card card-front" aria-label="Business card front">
    <span class="wordmark">PAVREL</span>
  </section>

  <section class="card card-back" aria-label="Business card back">
    <div class="info-panel">
      <p class="person-name">Daniel Harper</p>
      <p class="person-title">Owner</p>
      <div class="contact-block">
        <p class="address">418 Linden Ave, #112<br>Marlow, OH 43210</p>
        <ul class="contact-list">
          <li>
            <svg viewBox="0 0 16 16" aria-hidden="true"><circle cx="8" cy="8" r="8" fill="#f3f5f2"/><path d="M5.2 4.2l1.4-.3.8 2-1 .8c.5 1.1 1.2 1.8 2.3 2.3l.8-1 2 .8-.3 1.4c-3.4.3-6.3-2.6-6-6z" fill="#263b29"/></svg>
            614-555-0142
          </li>
          <li>
            <svg viewBox="0 0 16 16" aria-hidden="true"><rect x="1" y="3" width="14" height="10" rx="1" fill="#f3f5f2"/><path d="M1.5 3.8L8 9l6.5-5.2" fill="none" stroke="#263b29" stroke-width="1.2"/></svg>
            info@pavrel.com
          </li>
          <li>
            <svg viewBox="0 0 16 16" aria-hidden="true"><circle cx="8" cy="8" r="7.5" fill="#f3f5f2"/><g fill="none" stroke="#263b29" stroke-width="1"><ellipse cx="8" cy="8" rx="3" ry="7"/><path d="M1 8h14M2.5 4.5h11M2.5 11.5h11"/></g></svg>
            www.pavrel.com
          </li>
        </ul>
      </div>
    </div>
    <div class="brand-panel">
      <span class="wordmark">PAVREL</span>
    </div>
  </section>
</main>
</body>
</html>
```